Industry automation wholesale website

www.velturo.eu provides solutions for automation, building automation and digital signage.

Our products are rugged, reliable, energy saving and representative.

Scope of pages:
● welcome page
- scope of products
- applications, success stories and news
● category page
- short introduction
- sub categories
- product highlights
● product page
- short introduction
- about 3 to 4 pictures
- technical specifications: materials, dimensions
- price
- related products

Optional:
● contact page
- address
- contact form
● blog
- picture
- text
● logo
● favicon / apple touch icon

Conclusion:
● We need a professionally looking site
● Bright colors (e.g. white, grey, metalic colors, blue)

some pages we like:
http://www.prandek.de/
http://www.morvalix.de/

Target Market(s)

Our target market is the industrial sector
● Target audience: engineering and IT professionals

Industry/Entity Type

Building

Requirements
Must have
• ● only use free available fonts e.g. Lumara Type Library (http://www.lumaratype.com/webfonts)
Should not have
• ● sound
● flash

```html
<!DOCTYPE html>
<html lang="en">
<head>
<meta charset="utf-8">
<title>Velturo – Analog Digital Measurements</title>
<link rel="stylesheet" href="https://fonts.googleapis.com/css2?family=Montserrat:wght@400;600;700&family=Open+Sans:wght@400;600&family=Noto+Serif:wght@400&display=swap">
<style>
:root{
  --blue:#1a8fd6;
  --blue-dark:#0d4fa8;
  --blue-deep:#0a3c8a;
  --navy:#16293a;
  --sky:#def0fc;
  --ink:#2a2f36;
  --grey:#6b7077;
  --line:#d9dde2;
  --white:#ffffff;
}
*{margin:0;padding:0;box-sizing:border-box}
html,body{width:1200px;height:3097px;overflow:hidden;background:var(--white)}
body{position:relative;font-family:"Open Sans",Arial,sans-serif;color:var(--ink)}
a{color:inherit;text-decoration:none}

/* header */
.site-header{position:absolute;top:0;left:0;width:1200px;height:175px;background:var(--white);border-top:5px solid var(--blue)}
.brand{position:absolute;left:40px;top:70px;display:flex;align-items:center;gap:14px}
.brand-name{font-family:"Montserrat",sans-serif;font-weight:600;font-size:46px;color:var(--blue-dark);letter-spacing:1px}
.brand-mark{width:18px;height:18px;background:var(--blue)}
.brand-tag{position:absolute;left:40px;top:124px;font-family:"Montserrat",sans-serif;font-size:13px;color:var(--blue-dark);letter-spacing:.5px}
.utility{position:absolute;right:42px;top:24px;display:flex;gap:36px;font-family:"Montserrat",sans-serif;font-size:12px;color:var(--blue-dark)}
.main-nav{position:absolute;right:42px;top:104px;display:flex;gap:38px;font-family:"Montserrat",sans-serif;font-size:12px;font-weight:600;color:var(--blue-deep);align-items:center}
.main-nav .active{color:var(--blue);position:relative}
.main-nav .active::after{content:"";position:absolute;left:-8px;right:-8px;top:57px;height:5px;background:var(--blue)}

/* hero */
.hero{position:absolute;top:175px;left:0;width:1200px;height:434px;background:linear-gradient(180deg,#9fc9e6 0%,#5fa3d2 55%,#4f91c4 100%)}
.hero-inner{position:absolute;left:0;top:140px;width:1200px;text-align:center;color:var(--white)}
.hero h1{font-family:"Noto Serif",Georgia,serif;font-weight:400;font-size:27px;line-height:1.3;margin-top:18px}
.hero-arrow{position:absolute;top:192px;width:44px;height:44px;background:var(--white);display:flex;align-items:center;justify-content:center}
.hero-arrow.prev{left:0}.hero-arrow.next{right:0}

/* about */
.about{position:absolute;top:609px;left:0;width:1200px;height:707px;background:var(--sky)}
.section-title{font-family:"Noto Serif",Georgia,serif;font-weight:400;font-size:24px;letter-spacing:1px;text-align:center}
.about .section-title{color:var(--blue);margin-top:108px}
.about p{width:760px;margin:32px auto 0;text-align:center;font-family:"Noto Serif",Georgia,serif;font-size:15px;line-height:1.6;color:var(--ink)}
.more{font-family:"Montserrat",sans-serif;font-size:10px;font-weight:700;color:var(--blue)}
.about .more{display:block;text-align:center;margin-top:50px}
.feature{position:absolute;top:415px;width:362px;height:246px;background:var(--navy);text-align:center}
.feature h2{font-family:"Noto Serif",Georgia,serif;font-weight:400;font-size:20px;color:var(--blue);margin-top:50px;letter-spacing:1px}
.feature p{width:300px;margin:18px auto 0;font-size:12.5px;line-height:1.6;color:#d6dde3}
.feature-icon{position:absolute;right:58px;top:-38px;width:56px;height:56px;background:var(--blue);display:flex;align-items:center;justify-content:center}
.feature-icon::after{content:"";position:absolute;bottom:-10px;left:10px;border-top:10px solid var(--blue);border-right:10px solid transparent}

/* products */
.products{position:absolute;top:1316px;left:0;width:1200px;height:709px}
.products .section-title{color:var(--ink);margin-top:96px}
.product{position:absolute;top:168px;width:270px}
.product-image{height:225px;background:radial-gradient(circle at 50% 45%,#c9d3de 0%,#eef1f4 70%)}
.product h3{font-weight:600;font-size:20px;line-height:1.25;color:var(--blue-dark);margin-top:30px}
.product p{font-size:12px;line-height:1.6;color:var(--grey);margin-top:16px;width:250px}
.product .more{display:block;margin-top:30px}
.divider-v{position:absolute;top:190px;width:1px;height:470px;background:var(--line)}

/* call band */
.call-band{position:absolute;top:2025px;left:0;width:1200px;height:158px;background:linear-gradient(100deg,var(--blue-deep) 0%,#1c6fc9 45%,#0f4ea6 100%);display:flex;align-items:center;justify-content:center;color:var(--white);font-size:26px;font-weight:600}

/* news + testimony */
.news{position:absolute;top:2183px;left:95px;width:680px}
.col-title{font-family:"Noto Serif",Georgia,serif;font-weight:400;font-size:24px;color:var(--ink);margin-top:80px}
.news-item{margin-top:18px;padding-bottom:14px;border-bottom:1px solid var(--line)}
.news-item:last-of-type{border-bottom:none}
.news-date{font-size:10px;font-weight:600;color:var(--blue)}
.news-item p{font-size:11px;line-height:1.55;color:var(--grey);margin-top:2px}
.news-item strong{font-size:15px;color:var(--blue-dark);font-weight:600}
.news .more{display:block;margin-top:10px}
.news-line{position:absolute;top:2262px;left:788px;width:1px;height:430px;background:var(--line)}
.testimony{position:absolute;top:2183px;left:831px;width:284px;text-align:center}
.testimony .col-title{text-align:center}
.testimony-photo{height:183px;margin-top:26px;background:linear-gradient(160deg,#cfd9e3 0%,#8fa6bd 60%,#4c607a 100%)}
.testimony cite{display:block;font-style:normal;font-size:10px;color:var(--ink);margin-top:40px}
.testimony blockquote{font-size:11.5px;font-style:italic;line-height:1.5;color:var(--blue);margin-top:6px}
.testimony .more{display:block;margin-top:14px}

/* footer */
.site-footer{position:absolute;top:2755px;left:0;width:1200px;height:290px;background:linear-gradient(115deg,#0b4da3 0%,#1466c4 40%,#2a8ee0 75%,#1666c0 100%);color:var(--white)}
.foot-col{position:absolute;top:48px;font-size:11px;line-height:1.55}
.foot-col h4{font-family:"Montserrat",sans-serif;font-size:11px;font-weight:700;margin-bottom:14px}
.newsletter{position:absolute;left:832px;top:48px;width:290px}
.newsletter h4{font-family:"Montserrat",sans-serif;font-size:11px;font-weight:700}
.newsletter p{font-size:10.5px;margin-top:10px}
.signup{display:flex;margin-top:12px}
.signup span{flex:1;height:30px;background:var(--white);color:#9aa0a6;font-size:10.5px;line-height:30px;padding-left:10px}
.signup b{width:36px;height:30px;background:var(--navy);font-size:11px;line-height:30px;text-align:center}
.bottom-bar{position:absolute;top:3045px;left:0;width:1200px;height:52px;background:var(--white);font-family:"Montserrat",sans-serif;font-size:9px;color:var(--grey);padding:20px 0 0 95px;letter-spacing:.5px}
</style>
</head>
<body>

<header class="site-header">
  <div class="brand"><span class="brand-name">velturo</span><span class="brand-mark"></span></div>
  <div class="brand-tag">analog digital measurements</div>
  <nav class="utility"><a>Sign Out</a><a>My Account ▾</a><a>English ▾</a><a>🛒 0€</a></nav>
  <nav class="main-nav">
    <a class="active">HOME</a><a>PRODUCTS</a><a>APPLICATIONS</a><a>SUPPORT</a><a>ABOUT US</a><a>CONTACT</a>
    <svg width="14" height="14" viewBox="0 0 14 14"><circle cx="6" cy="6" r="4.5" fill="none" stroke="#0a3c8a" stroke-width="2"/><path d="M9.5 9.5L13 13" stroke="#0a3c8a" stroke-width="2"/></svg>
  </nav>
</header>

<section class="hero" role="img" aria-label="Photo of people walking through a bright modern industrial hall, tinted blue">
  <div class="hero-inner">
    <svg width="60" height="54" viewBox="0 0 60 54"><rect x="3" y="3" width="54" height="36" fill="none" stroke="#fff" stroke-width="5"/><rect x="22" y="40" width="16" height="7" fill="#fff"/><rect x="14" y="47" width="32" height="5" fill="#fff"/></svg>
    <h1>Velturo is your specialist partner<br>for industrial automation.</h1>
  </div>
  <a class="hero-arrow prev"><svg width="12" height="18" viewBox="0 0 12 18"><path d="M10 2L3 9l7 7" fill="none" stroke="#16293a" stroke-width="3"/></svg></a>
  <a class="hero-arrow next"><svg width="12" height="18" viewBox="0 0 12 18"><path d="M2 2l7 7-7 7" fill="none" stroke="#16293a" stroke-width="3"/></svg></a>
</section>

<section class="about">
  <h2 class="section-title">ABOUT US</h2>
  <p>Eum ex, laoreet iudicabit posid onium quo te. Mei ex legere civibus phaedrum. Id eam putent conceptam. Ad malis nihil epicurei dolorum torquatos ut, cu prolegere civibus phaedrum. Id eam putent conceptam movet debitis graecis.Eum ex, laoreet iudicabit posid onium quo te. Mei ex legere civibus phaedrum. Id eam putent conceptam. Ad malis nihil epicurei dolorum torquatos ut, cu prolegere civibus phaedrum.</p>
  <a class="more">READ MORE HERE</a>

  <article class="feature" style="left:41px">
    <span class="feature-icon"><svg width="28" height="24" viewBox="0 0 28 24"><rect x="2" y="2" width="24" height="15" fill="none" stroke="#fff" stroke-width="3"/><rect x="10" y="18" width="8" height="3" fill="#fff"/><rect x="6" y="21" width="16" height="2" fill="#fff"/></svg></span>
    <h2>PRODUCTS</h2>
    <p>Eum ex, laoreet iudicabit posid onium quo te. Mei ex legere civibus phaedrum. Id eam putent conceptam. Ad malis nihil epicurei dolorum torquatos ut, cu prolegere civibus phaedrum. Id eam putent conceptam movet debitis graecis.</p>
  </article>
  <article class="feature" style="left:419px">
    <span class="feature-icon"><svg width="26" height="26" viewBox="0 0 26 26"><path d="M4 22L13 3l9 19M8 15h10" fill="none" stroke="#fff" stroke-width="3"/></svg></span>
    <h2>APPLICATIONS</h2>
    <p>Eum ex, laoreet iudicabit posid onium quo te. Mei ex legere civibus phaedrum. Id eam putent conceptam. Ad malis nihil epicurei dolorum torquatos ut, cu prolegere civibus phaedrum. Id eam putent conceptam movet debitis graecis.</p>
  </article>
  <article class="feature" style="left:797px">
    <span class="feature-icon"><svg width="26" height="26" viewBox="0 0 26 26"><circle cx="13" cy="13" r="7" fill="none" stroke="#fff" stroke-width="5" stroke-dasharray="3 2.5"/><circle cx="13" cy="13" r="5" fill="none" stroke="#fff" stroke-width="3"/></svg></span>
    <h2>SUPPORT</h2>
    <p>Eum ex, laoreet iudicabit posid onium quo te. Mei ex legere civibus phaedrum. Id eam putent conceptam. Ad malis nihil epicurei dolorum torquatos ut, cu prolegere civibus phaedrum. Id eam putent conceptam movet debitis graecis.</p>
  </article>
</section>

<section class="products">
  <h2 class="section-title">LATEST PRODUCTS</h2>
  <article class="product" style="left:95px">
    <div class="product-image" role="img" aria-label="Widescreen industrial display monitor with purple screen"></div>
    <h3>Eum ex, laoreet iudicabit posid onium quo te.</h3>
    <p>Mei ex legere civibus phaedrum. Id eam putent conceptam. Ad malis nihil epicurei dolorum torquatos ut, prolegere ipsum.</p>
    <a class="more">READ MORE HERE</a>
  </article>
  <span class="divider-v" style="left:410px"></span>
  <article class="product" style="left:487px">
    <div class="product-image" role="img" aria-label="Touchscreen panel showing an on-screen keypad"></div>
    <h3>Eum ex, laoreet iudicabit posid onium quo te.</h3>
    <p>Mei ex legere civibus phaedrum. Id eam putent conceptam. Ad malis nihil epicurei dolorum torquatos ut, prolegere ipsum.</p>
    <a class="more">READ MORE HERE</a>
  </article>
  <span class="divider-v" style="left:790px"></span>
  <article class="product" style="left:865px">
    <div class="product-image" role="img" aria-label="Two grey standing information terminals on pedestals"></div>
    <h3>Eum ex, laoreet iudicabit posid onium quo te.</h3>
    <p>Mei ex legere civibus phaedrum. Id eam putent conceptam. Ad malis nihil epicurei dolorum torquatos ut, prolegere ipsum.</p>
    <a class="more">READ MORE HERE</a>
  </article>
</section>

<section class="call-band">Have a question? Call us at +49 211 540 27 93 or info@velturo.de</section>

<section class="news">
  <h2 class="col-title">NEWS</h2>
  <article class="news-item">
    <div class="news-date">Dec/03</div>
    <p><strong>Eum ex, laoreet iudicabit posid onium quo te.</strong> Mei ex legere civibus phaedrum. Id eam putent conceptam. Ad malis nihil epicurei dolorum torquatos ut, cu prolegere civibus phaedrum. Id eam putent conceptam movet debitis graecis.Eum ex, laoreet iudicabit posid onium quo te. Mei ex legere civibus phaedrum. Id eam putent conceptam movet debitis Ad malis nihil epicurei dolorum torquatos ut, cu prolegere civibus phaedrum. [...]</p>
  </article>
  <article class="news-item">
    <div class="news-date">Dec/15</div>
    <p><strong>Eum ex, laoreet iudicabit posid onium quo te.</strong> Mei ex legere civibus phaedrum. Id eam putent conceptam. Ad malis nihil epicurei dolorum torquatos ut, cu prolegere civibus phaedrum. Id eam putent conceptam movet debitis Ad malis nihil epicurei dolorum torquatos ut, cu prolegere civibus phaedrum. Id eam putent conceptam movet debitis Ad malis nihil epicurei dolorum torquatos ut, cu prolegere. [...]</p>
  </article>
  <article class="news-item">
    <div class="news-date">Dec/27</div>
    <p><strong>Eum ex, laoreet iudicabit posid onium quo te.</strong> Mei ex legere civibus phaedrum. Id eam putent conceptam. Ad malis nihil epicurei dolorum torquatos ut, cu prolegere civibus phaedrum. Id eam putent conceptam movet debitis graecis.Eum ex, laoreet iudicabit posid onium quo te. Mei ex legere civibus phaedrum. Id eam putent conceptam movet debitis Ad malis nihil epicurei dolorum torquatos ut, cu prolegere civibus phaedrum. [...]</p>
  </article>
  <a class="more">READ MORE HERE</a>
</section>

<span class="news-line"></span>

<aside class="testimony">
  <h2 class="col-title">TESTEMONY</h2>
  <div class="testimony-photo" role="img" aria-label="Photo of a smiling businessman in an office with colleagues behind him"></div>
  <cite>Jonas Hale, CEO of Norvanta</cite>
  <blockquote>“Mei ex legere civibus phaedrum. Id eam putent conceptam. Ad malis nihil epicurei dolorum torquatos ut, cu prolegere civibus phaedrum. Id eam putent conceptam movet debitis Ad malis nihil epicurei dolorum onium quo te.” [...]</blockquote>
  <a class="more">READ MORE HERE</a>
</aside>

<footer class="site-footer">
  <div class="foot-col" style="left:95px">
    <h4>MAIN MENU</h4>
    Home<br>Products<br>Applications<br>Support<br>About Us<br>Contact
  </div>
  <div class="foot-col" style="left:219px">
    <h4>OTHER OPTIONS</h4>
    News<br>Testemony<br>Privacy &amp; Legal<br>FAQs<br>Help<br>Site Map
  </div>
  <div class="foot-col" style="left:372px">
    <h4>CONTACT</h4>
    Velturo Mertens<br>Lindenallee 14<br>40212 Düsseldorf<br><br>Phone: +49 211 540 27 93<br>Telefax: +49 211 540 27 94<br>Email: info@velturo.de
  </div>
  <div class="newsletter">
    <h4>NEWSLETTER</h4>
    <p>Sign up now to receive our regular emails</p>
    <div class="signup"><span>Enter your email address</span><b>Go</b></div>
  </div>
</footer>

<div class="bottom-bar">VELTURO – ANALOG DIGITAL MEASUREMENTS | ALL RIGHTS RESERVED © 2014</div>

</body>
</html>
```